Marlow Sail Works President Business Card Carbon fiber catamarans

Hi.. I need a new business card design.. I am the President of a high tech yacht builder. We build Carbon Fiber go fast catamarans... Maybe we use the file I am sharing to you as the back of the card.. We need to look cool and crisp ...

Target Market(s)

Affluent People who will purchase a cool yacht

Industry/Entity Type

Custom Yacht Builder

Contact Information for Business Card

Dean Pellway , President, 731.508.2164 USA

Font styles to use
Serif

Requirements
Must have
• the clean crisp cool feel
Nice to have
• clean and crisp
Should not have
• Bold ugly

```html
<!DOCTYPE html>
<html lang="en">
<head>
<meta charset="utf-8">
<title>Marlow Sail Works – Business Card</title>
<link href="https://fonts.googleapis.com/css2?family=Oswald:wght@500&family=Saira:wght@300;400&display=swap" rel="stylesheet">
<style>
  :root {
    --backdrop: #3b3b3b;
    --card-dark: #111111;
    --card-mid: #1d1d1d;
    --text-light: #e4e4e4;
    --text-soft: #cfcfcf;
    --silver-a: #9c9c9c;
    --silver-b: #e6e6e6;
    --rule: #8a8a8a;
  }
  * { box-sizing: border-box; margin: 0; padding: 0; }
  html, body { width: 1125px; height: 1200px; overflow: hidden; }
  body {
    background: var(--backdrop);
    font-family: "Saira", "Helvetica Neue", Arial, sans-serif;
    color: var(--text-light);
    position: relative;
  }
  .card {
    position: absolute;
    left: 171px;
    width: 826px;
    height: 471px;
    overflow: hidden;
    box-shadow: 0 6px 16px rgba(0,0,0,.45);
  }
  .card--front { top: 106px; }
  .card--back { top: 624px; }
  .card__texture {
    position: absolute; inset: 0;
    background: linear-gradient(135deg, var(--card-mid) 0%, var(--card-dark) 55%, var(--card-mid) 100%);
  }
  .card__band {
    position: absolute; left: 0; right: 0; bottom: 0; height: 12px;
    background: linear-gradient(90deg, var(--silver-a), var(--silver-b) 50%, var(--silver-a));
  }
  .brand {
    position: absolute;
    left: 47px; top: 86px;
    font-weight: 400;
    font-size: 34px;
    letter-spacing: 5px;
    text-transform: uppercase;
    color: var(--text-light);
  }
  .address {
    position: absolute;
    left: 47px; top: 227px;
    font-weight: 300;
    font-size: 21px;
    line-height: 26px;
    color: var(--text-soft);
  }
  .contact-list {
    position: absolute;
    left: 47px; top: 290px;
    list-style: none;
  }
  .contact-list li {
    display: flex; align-items: center;
    height: 26px;
    font-weight: 300;
    font-size: 21px;
    color: var(--text-soft);
  }
  .contact-list svg {
    width: 18px; height: 18px; margin-right: 13px;
    fill: var(--text-soft);
  }
  .contact-list li.is-phone { font-size: 22px; }
  .person {
    position: absolute;
    right: 55px; top: 290px;
    text-align: right;
  }
  .person__name {
    font-family: "Oswald", "Arial Narrow", sans-serif;
    font-weight: 500;
    font-size: 36px;
    letter-spacing: 1px;
    text-transform: uppercase;
    color: var(--text-light);
    line-height: 44px;
  }
  .person__title {
    font-weight: 400;
    font-size: 20px;
    color: var(--text-soft);
  }
  .back-brand {
    position: absolute;
    left: 0; right: 0; top: 170px;
    text-align: center;
    font-weight: 400;
    font-size: 46px;
    letter-spacing: 7px;
    text-transform: uppercase;
    color: var(--text-light);
  }
  .social {
    position: absolute;
    left: 0; right: 0; top: 379px;
    display: flex; justify-content: center; align-items: center; gap: 7px;
  }
  .social__rule { width: 100px; height: 1px; background: var(--rule); margin: 0 6px; }
  .social__dot { width: 26px; height: 26px; border-radius: 50%; background: var(--text-light); }
</style>
</head>
<body>

<section class="card card--front">
  <div class="card__texture" role="img" aria-label="Carbon fibre weave texture"></div>
  <div class="brand">Marlow Sail Works</div>
  <p class="address">418 Keelson Way<br>Port Alder, Maine 04102</p>
  <ul class="contact-list">
    <li class="is-phone">
      <svg viewBox="0 0 24 24"><path d="M6.6 10.8a15.1 15.1 0 0 0 6.6 6.6l2.2-2.2c.3-.3.7-.4 1-.2 1.1.4 2.3.6 3.6.6.6 0 1 .4 1 1V20c0 .6-.4 1-1 1A17 17 0 0 1 3 4c0-.6.4-1 1-1h3.5c.6 0 1 .4 1 1 0 1.3.2 2.5.6 3.6.1.3 0 .7-.2 1z"/></svg>
      731.508.2164
    </li>
    <li class="is-phone">
      <svg viewBox="0 0 24 24"><path d="M7 1h10a2 2 0 0 1 2 2v18a2 2 0 0 1-2 2H7a2 2 0 0 1-2-2V3a2 2 0 0 1 2-2zm0 3v14h10V4z"/></svg>
      731.508.4390
    </li>
    <li class="is-phone">
      <svg viewBox="0 0 24 24"><path d="M7 3h10v5H7zM3 9h18v8h-3v4H6v-4H3zm5 6v4h8v-4z"/></svg>
      731.508.7712
    </li>
    <li>
      <svg viewBox="0 0 24 24"><path d="M3 6h18v12H3zm1.5 1.5V8l7.5 5 7.5-5v-.5z"/></svg>
      name@marlowsail.com
    </li>
    <li>
      <svg viewBox="0 0 24 24"><circle cx="12" cy="12" r="9"/></svg>
      www.marlowsail.com
    </li>
  </ul>
  <div class="person">
    <div class="person__name">Dean Pellway</div>
    <div class="person__title">President</div>
  </div>
  <div class="card__band"></div>
</section>

<section class="card card--back">
  <div class="card__texture" role="img" aria-label="Carbon fibre weave texture"></div>
  <div class="back-brand">Marlow Sail Works</div>
  <div class="social">
    <span class="social__rule"></span>
    <span class="social__dot"></span>
    <span class="social__dot"></span>
    <span class="social__dot"></span>
    <span class="social__rule"></span>
  </div>
  <div class="card__band"></div>
</section>

</body>
</html>
```